Flyer für ambulanten Pflegedienst
Zielgruppe
Ambulanter Pflegedienst, Potentielle Kunden für Grund- und Behandlungspflege, nicht nur Pflegebedürftige, sondern auch Angehörige. Flyer dient zur Auslage, beispielsweise in Wartezimmern von Ärzten.
Aufgabenstellung
Ausführliches Briefing mit Aufbau und Text in der Anlage, ebenso das Bildmaterial, Fonts, Logos. Flyer in A4 Wickelfalz, bitte die Gestaltungsvorlage mit den Maßen des Druckanbieters (ebenfalls anbei) beachten. Vorerst hauptsächlich KI-generierte/Stockfotos vorhanden, Fotoshooting folgt im Juli und Bilder werden dann ggf. nochmal ersetzt um persönliche Ebene zu erzeugen. Der erste Wurf muss aber vorerst so erfolgen. Übergabe der Daten: Druckfähiges PDF, PDF mit Ebenen und AI

```html
<!DOCTYPE html>
<html lang="de">
<head>
<meta charset="utf-8">
<title>Flyer Pflege Wendrich</title>
<link rel="stylesheet" href="https://fonts.googleapis.com/css2?family=Montserrat:wght@500;700;800&family=Open+Sans:wght@400;600;700&display=swap">
<style>
:root{
  --blue:#1b3f99;
  --blue-dark:#12306f;
  --green:#2f9a4a;
  --ink:#1c1f26;
  --muted:#5b6270;
  --paper:#ffffff;
  --panel-alt:#f6f7fa;
  --line:#dfe3ea;
  --bg:#e9e6e1;
}
*{box-sizing:border-box;margin:0;padding:0}
html,body{width:1200px;height:670px;overflow:hidden;background:var(--bg)}
body{position:relative;font-family:"Open Sans",sans-serif;color:var(--ink)}
.sheet{position:absolute;top:129px;width:582px;height:412px;display:flex;background:var(--paper);box-shadow:0 2px 8px rgba(0,0,0,.12)}
.sheet--inside{left:12px}
.sheet--outside{left:606px}
.panel{position:relative;width:194px;height:100%;padding:14px 13px;overflow:hidden;border-right:1px solid var(--line)}
.panel:last-child{border-right:none}
.panel--alt{background:var(--panel-alt)}
.photo{position:relative;background:linear-gradient(135deg,#b99b83,#6f8fb8);}
.photo--circle{border-radius:50%;border:4px solid var(--blue)}
.h-head{font-family:"Montserrat",sans-serif;font-weight:800;text-transform:uppercase;line-height:1.08;color:var(--ink)}
.h-head .hl{color:var(--blue)}
.h-head .hl-green{color:var(--green)}
.kicker{font-family:"Montserrat",sans-serif;font-weight:600;font-size:8px;color:var(--blue);margin-bottom:3px}
.body{font-size:6.2px;line-height:1.45;color:var(--muted);margin-bottom:6px}
.wave{position:absolute;left:0;bottom:0;width:100%;height:34px}
/* cover */
.cover-photo{width:150px;height:108px;margin:0 auto 8px;border-radius:0 0 80px 80px}
.brand{position:absolute;top:102px;left:50%;transform:translateX(-50%);display:flex;align-items:center;gap:4px;background:var(--paper);border-radius:20px;padding:4px 9px;box-shadow:0 1px 3px rgba(0,0,0,.2)}
.brand__dot{width:8px;height:8px;border-radius:50%;background:var(--blue)}
.brand__name{font-family:"Montserrat",sans-serif;font-weight:700;font-size:7px;color:var(--blue)}
.cover-title{font-size:13px;text-align:center;margin-top:22px}
.pill{margin:9px auto 8px;background:var(--blue);color:#fff;border-radius:14px;padding:5px 8px;text-align:center;font-size:7.2px;font-weight:600;line-height:1.3}
.ticks{list-style:none;padding-left:6px}
.ticks li{display:flex;align-items:center;gap:4px;font-size:7px;font-weight:600;margin-bottom:2px}
.ticks svg{width:8px;height:8px}
/* services list */
.service{display:flex;gap:6px;align-items:flex-start;border:1px solid var(--line);border-radius:6px;padding:5px 6px;margin-bottom:5px;background:var(--paper)}
.service__icon{flex:none;width:15px;height:15px;border-radius:50%;background:var(--blue);display:flex;align-items:center;justify-content:center}
.service__icon svg{width:8px;height:8px}
.service--green .service__icon{background:var(--green)}
.service__title{font-family:"Montserrat",sans-serif;font-weight:700;font-size:7px;margin-bottom:1px}
.service__text{font-size:5.8px;line-height:1.35;color:var(--muted)}
.quote{border:1.5px solid var(--blue);border-radius:8px;padding:6px 8px;margin:6px 0;font-family:"Montserrat",sans-serif;font-weight:700;font-size:8px;color:var(--blue);line-height:1.25}
.contact{font-size:6px;line-height:1.5;color:var(--ink)}
.contact strong{font-family:"Montserrat",sans-serif;font-size:6.5px}
.green-foot{position:absolute;left:0;bottom:0;width:100%;height:58px;background:var(--green);color:#fff;padding:16px 13px 0;border-radius:50% 50% 0 0/22px 22px 0 0}
.green-foot__name{font-family:"Montserrat",sans-serif;font-weight:700;font-size:7px;text-align:center;margin-bottom:3px}
.green-foot__line{font-size:5.8px;text-align:center;line-height:1.4}
</style>
</head>
<body>

<section class="sheet sheet--inside">
  <!-- Cover -->
  <div class="panel">
    <div class="photo cover-photo photo--circle" role="img" aria-label="Foto: Pflegerin lächelt einer älteren Patientin zu"></div>
    <div class="brand"><span class="brand__dot"></span><span class="brand__name">Pflege Wendrich</span></div>
    <h1 class="h-head cover-title">Weil das <span class="hl">eigene</span> Zuhause <span class="hl">Lebensqualität ist.</span></h1>
    <div class="pill">Ihr ambulanter Pflegedienst für die Region.</div>
    <ul class="ticks">
      <li><svg viewBox="0 0 10 10"><circle cx="5" cy="5" r="5" fill="#1b3f99"/><path d="M2.8 5.2l1.5 1.5 3-3" stroke="#fff" stroke-width="1.3" fill="none"/></svg>24h erreichbar</li>
      <li><svg viewBox="0 0 10 10"><circle cx="5" cy="5" r="5" fill="#1b3f99"/><path d="M2.8 5.2l1.5 1.5 3-3" stroke="#fff" stroke-width="1.3" fill="none"/></svg>Persönliche Beratung</li>
      <li><svg viewBox="0 0 10 10"><circle cx="5" cy="5" r="5" fill="#1b3f99"/><path d="M2.8 5.2l1.5 1.5 3-3" stroke="#fff" stroke-width="1.3" fill="none"/></svg>MD-geprüfte Qualität</li>
    </ul>
    <svg class="wave" viewBox="0 0 194 34" preserveAspectRatio="none"><path d="M0 14 Q97 34 194 0 V34 H0Z" fill="#1b3f99"/></svg>
  </div>

  <!-- Wer wir sind -->
  <div class="panel">
    <p class="kicker">Wer wir sind</p>
    <h2 class="h-head" style="font-size:12.5px;margin-bottom:8px">Vertrauen <span class="hl">beginnt</span> mit Zuhören.</h2>
    <p class="body">Pflege bedeutet für uns mehr als Versorgung. Es geht um Zeit, Nähe und das Gefühl, zu Hause gut begleitet zu werden.</p>
    <p class="body">Unser erfahrenes Team kennt die Region und nimmt sich Zeit für Ihre Fragen, Sorgen und Wünsche im Alltag.</p>
    <p class="body">Als inhabergeführter Pflegedienst begleiten wir Menschen mit Respekt, Ruhe und echter Verlässlichkeit.</p>
    <div class="photo photo--circle" style="width:140px;height:140px;margin:8px auto 0;position:relative;z-index:1" role="img" aria-label="Foto: Pflegerin misst den Blutdruck einer Seniorin im Wohnzimmer"></div>
    <svg class="wave" style="height:60px" viewBox="0 0 194 60" preserveAspectRatio="none"><path d="M0 30 Q97 70 194 20 V60 H0Z" fill="#1b3f99"/></svg>
  </div>

  <!-- Leistungen -->
  <div class="panel">
    <p class="kicker">Unsere Leistungen</p>
    <h2 class="h-head" style="font-size:12px;margin-bottom:9px">Unterstützung, <span class="hl">die den Alltag</span> leichter <span class="hl">macht.</span></h2>
    <div class="service"><span class="service__icon"><svg viewBox="0 0 10 10"><circle cx="5" cy="3.5" r="2" fill="#fff"/><path d="M1.5 9.5a3.5 3 0 0 1 7 0Z" fill="#fff"/></svg></span><div><p class="service__title">Grundpflege</p><p class="service__text">Hilfe bei Körperpflege, Ernährung und Mobilität im Alltag.</p></div></div>
    <div class="service"><span class="service__icon"><svg viewBox="0 0 10 10"><path d="M4 1h2v3h3v2H6v3H4V6H1V4h3Z" fill="#fff"/></svg></span><div><p class="service__title">Behandlungspflege</p><p class="service__text">Ärztlich verordnete Leistungen wie Wundversorgung und Medikamentengabe.</p></div></div>
    <div class="service"><span class="service__icon"><svg viewBox="0 0 10 10"><path d="M5 9 1.5 5.5a2 2 0 0 1 3.5-2.5 2 2 0 0 1 3.5 2.5Z" fill="#fff"/></svg></span><div><p class="service__title">Betreuung &amp; Alltagsbegleitung</p><p class="service__text">Gesellschaft, Gespräche und Unterstützung bei täglichen Aufgaben.</p></div></div>
    <div class="service"><span class="service__icon"><svg viewBox="0 0 10 10"><circle cx="3.3" cy="3.5" r="1.5" fill="#fff"/><circle cx="6.7" cy="3.5" r="1.5" fill="#fff"/><path d="M0.8 8.5a2.5 2.3 0 0 1 5 0ZM4.2 8.5a2.5 2.3 0 0 1 5 0Z" fill="#fff"/></svg></span><div><p class="service__title">Verhinderungspflege</p><p class="service__text">Zuverlässige Vertretung, wenn Angehörige eine Pause brauchen.</p></div></div>
    <div class="service"><span class="service__icon"><svg viewBox="0 0 10 10"><path d="M1 2h8v5H4l-2 2V7H1Z" fill="#fff"/></svg></span><div><p class="service__title">Beratung</p><p class="service__text">Beratung nach § 37.3 SGB XI und Hilfe bei Anträgen.</p></div></div>
    <svg class="wave" style="height:22px" viewBox="0 0 194 22" preserveAspectRatio="none"><path d="M0 6 Q97 26 194 14 V22 H0Z" fill="#1b3f99"/></svg>
  </div>
</section>

<section class="sheet sheet--outside">
  <!-- Weitere Leistungen -->
  <div class="panel">
    <h2 class="h-head" style="font-size:12px;margin-bottom:8px">Unsere<br><span class="hl">Leistungen</span></h2>
    <div class="service"><span class="service__icon"><svg viewBox="0 0 10 10"><path d="M2.5 1 4 3 3 4a5 5 0 0 0 3 3l1-1 2 1.5L8 9A7 7 0 0 1 1 2Z" fill="#fff"/></svg></span><div><p class="service__title">Hausnotruf &amp; Erreichbarkeit</p><p class="service__text">Schnelle Hilfe rund um die Uhr, direkt per Knopfdruck.</p></div></div>
    <div class="service"><span class="service__icon"><svg viewBox="0 0 10 10"><path d="M5 9 1.5 5.5a2 2 0 0 1 3.5-2.5 2 2 0 0 1 3.5 2.5Z" fill="#fff"/></svg></span><div><p class="service__title">Palliative Versorgung</p><p class="service__text">Einfühlsame Begleitung in der letzten Lebensphase, gemeinsam mit Ärzten und Angehörigen.</p></div></div>
    <blockquote class="quote">„Unsere Pflege orientiert sich am Befinden der Menschen – nicht am Befund.“</blockquote>
    <div class="photo" style="position:absolute;left:0;bottom:18px;width:100%;height:130px;background:linear-gradient(180deg,#c9d6e6,#7c8fa6 60%,#6f8a55)" role="img" aria-label="Foto: Pflegeteam in blauer Dienstkleidung am Dienstwagen"></div>
    <svg class="wave" style="height:22px" viewBox="0 0 194 22" preserveAspectRatio="none"><path d="M0 4 Q120 0 194 0 V22 H0Z" fill="#1b3f99"/></svg>
  </div>

  <!-- Was uns besonders macht -->
  <div class="panel panel--alt">
    <div class="photo photo--circle" style="width:120px;height:100px;margin:0 auto 10px;background:linear-gradient(180deg,#c8d7ea,#8aa3c4 60%,#7f9a5e)" role="img" aria-label="Foto: Pflegerin geht zum Dienstwagen"></div>
    <h2 class="h-head" style="font-size:12px;margin-bottom:6px">Was uns <span class="hl">besonders</span> macht.</h2>
    <p style="font-family:Montserrat,sans-serif;font-weight:600;font-size:7.5px;line-height:1.3;margin-bottom:5px">Gute Pflege entsteht durch Aufmerksamkeit, Erfahrung und ein verlässliches Team.</p>
    <p class="body">Wir nehmen uns Zeit, hören zu und stimmen jede Versorgung eng mit Ihnen und Ihrer Familie ab.</p>
    <p style="font-family:Montserrat,sans-serif;font-weight:700;font-size:8px;margin-bottom:3px">Wir sind für Sie da.</p>
    <p class="body">Rufen Sie uns an oder besuchen Sie uns – wir beraten Sie gerne persönlich.</p>
    <div class="contact">
      <strong>Hauswirtschaftspflege Wendrich</strong><br>
      Lindenweg 10 · 24103 Kiel<br>
      Tel. 0431 55 20 18<br>
      www.wendrich-pflege.de<br>
      Mo–Fr 8–16 Uhr, Termine nach Absprache
    </div>
  </div>

  <!-- Haushaltsdienst -->
  <div class="panel">
    <h2 class="h-head" style="font-size:12px;margin-bottom:3px">Haushaltsdienst<br><span class="hl-green">Leistungen</span></h2>
    <p style="font-size:6.8px;font-weight:700;margin-bottom:4px">Haushaltshilfe, Entlastung im Alltag.</p>
    <p class="body">Neben der Pflege unterstützen wir Sie auch im Haushalt, damit mehr Zeit für das Wesentliche bleibt.</p>
    <div class="service service--green"><span class="service__icon"><svg viewBox="0 0 10 10"><path d="M1 5 5 1.5 9 5H8v4H2V5Z" fill="#fff"/></svg></span><div><p class="service__title">Haushaltshilfe</p><p class="service__text">Einkaufen, Reinigen und Wäsche – ganz nach Bedarf.</p></div></div>
    <div class="service service--green"><span class="service__icon"><svg viewBox="0 0 10 10"><circle cx="5" cy="2.5" r="1.5" fill="#fff"/><path d="M3.5 4.5h3l-.5 5h-2Z" fill="#fff"/></svg></span><div><p class="service__title">Begleitung</p><p class="service__text">Begleitung zu Ärzten, Behörden und Terminen.</p></div></div>
    <div class="service service--green"><span class="service__icon"><svg viewBox="0 0 10 10"><path d="M5 9 1.5 5.5a2 2 0 0 1 3.5-2.5 2 2 0 0 1 3.5 2.5Z" fill="#fff"/></svg></span><div><p class="service__title">Pflege</p><p class="service__text">Pflege und Hauswirtschaft aus einer Hand.</p></div></div>
    <p style="font-family:Montserrat,sans-serif;font-weight:700;font-size:7.5px;text-align:center;margin-top:4px">So erreichen Sie uns</p>
    <p class="body" style="text-align:center;margin-bottom:0">Wir freuen uns auf Ihren Anruf.</p>
    <div class="photo" style="position:absolute;left:22px;bottom:44px;width:150px;height:52px;border-radius:6px;background:linear-gradient(90deg,#9fb0bf,#d6dde3)" role="img" aria-label="Foto: Mitarbeiterin im Büro"></div>
    <div class="green-foot">
      <p class="green-foot__name">Wendrich Home Services GmbH</p>
      <p class="green-foot__line">Tel. 0431 55 20 19 · info@wendrich-pflege.de<br>Lindenweg 10 · 24103 Kiel</p>
    </div>
  </div>
</section>

</body>
</html>
```